Business Card Design

We need a business card designed for our new company. Prefer a black card with white logo & writing.

Contact Information for Business Card

Ted Galloway, address: 7-4812 Fernhollow Road, Abbotsford, BC, V3K 8R2, Office Phone: 604-712-3390, Cell: 604-947-2164, Email: ted@resinworkshub.ca

Colors

Designer to choose only greyscale colors for use in the design.

```html
<!DOCTYPE html>
<html lang="en">
<head>
<meta charset="utf-8">
<title>Resinworks Hub — Business Card</title>
<link rel="stylesheet" href="https://fonts.googleapis.com/css2?family=Figtree:wght@400;600;800&display=swap">
<style>
  :root {
    --backdrop: #232323;
    --card-black: #000000;
    --card-white: #ffffff;
    --ridge-grey: #c1c1c1;
    --ink: #111111;
  }
  * { margin: 0; padding: 0; box-sizing: border-box; }
  html, body { width: 1200px; height: 900px; overflow: hidden; }
  body {
    background: var(--backdrop);
    font-family: "Figtree", "Helvetica Neue", Arial, sans-serif;
    position: relative;
  }
  .card {
    position: absolute;
    left: 341px;
    width: 518px;
    height: 296px;
    background: var(--card-black);
    overflow: hidden;
  }
  .card--front { top: 141px; }
  .card--back { top: 463px; }

  .mountain-art {
    position: absolute;
    inset: 0;
    background: linear-gradient(22deg,
      var(--card-white) 0%,
      var(--card-white) 48%,
      var(--ridge-grey) 56%,
      var(--ridge-grey) 60%,
      var(--card-black) 68%,
      var(--card-black) 100%);
  }

  .brand {
    position: absolute;
    color: var(--card-white);
    font-weight: 800;
    text-transform: uppercase;
    display: flex;
    align-items: center;
    white-space: nowrap;
  }
  .brand__mark {
    border: 2px solid var(--card-white);
    flex: none;
  }
  .brand--small {
    right: 26px; top: 70px;
    font-size: 15px; letter-spacing: 0.4px; gap: 7px;
  }
  .brand--small .brand__mark { width: 12px; height: 12px; }
  .brand--large {
    left: 50%; top: 50%;
    transform: translate(-50%, -50%);
    font-size: 38px; letter-spacing: 1px; gap: 14px;
  }
  .brand--large .brand__mark { width: 26px; height: 26px; border-width: 3px; }

  .holder-name {
    position: absolute;
    left: 27px; top: 181px;
    font-size: 19px; font-weight: 800;
    color: var(--ink);
    letter-spacing: 0.3px;
    text-transform: uppercase;
  }
  .contact {
    position: absolute;
    top: 218px;
    list-style: none;
    color: var(--ink);
    font-size: 14px;
    line-height: 18px;
  }
  .contact li { display: flex; align-items: center; gap: 6px; white-space: nowrap; }
  .contact--direct { left: 27px; }
  .contact--place { left: 229px; top: 217px; }
  .contact .icon { width: 12px; height: 12px; flex: none; }
  .contact .web-domain { font-weight: 600; }
  .contact .web-tld { font-weight: 400; }
  .divider {
    position: absolute;
    left: 211px; top: 221px;
    width: 1px; height: 48px;
    background: var(--ink);
  }
</style>
</head>
<body>

<section class="card card--front">
  <div class="mountain-art" role="img" aria-label="Stylised snowy mountain peak in white and grey rising from the lower left against black"></div>

  <div class="brand brand--small"><span class="brand__mark"></span>Resinworks Hub</div>

  <h1 class="holder-name">Ted Galloway</h1>

  <ul class="contact contact--direct">
    <li>
      <svg class="icon" viewBox="0 0 24 24" aria-hidden="true"><path fill="currentColor" d="M6.6 10.8a15.1 15.1 0 0 0 6.6 6.6l2.2-2.2a1 1 0 0 1 1-.25 11.4 11.4 0 0 0 3.6.57 1 1 0 0 1 1 1V20a1 1 0 0 1-1 1A17 17 0 0 1 3 4a1 1 0 0 1 1-1h3.5a1 1 0 0 1 1 1c0 1.25.2 2.45.57 3.57a1 1 0 0 1-.25 1z"/></svg>
      604-712-3390
    </li>
    <li>
      <svg class="icon" viewBox="0 0 24 24" aria-hidden="true"><rect x="6" y="2" width="12" height="20" rx="2" fill="none" stroke="currentColor" stroke-width="2"/><circle cx="12" cy="18" r="1.2" fill="currentColor"/></svg>
      604-947-2164
    </li>
    <li>
      <svg class="icon" viewBox="0 0 24 24" aria-hidden="true"><path fill="currentColor" d="M2 5h20v14H2z"/><path fill="none" stroke="#fff" stroke-width="2" d="M3 6l9 7 9-7"/></svg>
      ted@resinworkshub.ca
    </li>
  </ul>

  <span class="divider"></span>

  <ul class="contact contact--place">
    <li>7-4812 Fernhollow Road</li>
    <li>Abbotsford, BC, V3K 8R2</li>
    <li>
      <svg class="icon" viewBox="0 0 24 24" aria-hidden="true"><g fill="none" stroke="currentColor" stroke-width="1.8"><circle cx="12" cy="12" r="10"/><ellipse cx="12" cy="12" rx="4.5" ry="10"/><path d="M2 12h20M4 7h16M4 17h16"/></g></svg>
      <span><span class="web-domain">resinworkshub</span><span class="web-tld">.ca</span></span>
    </li>
  </ul>
</section>

<section class="card card--back">
  <div class="brand brand--large"><span class="brand__mark"></span>Resinworks Hub</div>
</section>

</body>
</html>
```